Design material for Lumora Event

We need a design of POSM for Lumora Event
1. Content:
- The Lumora Event 3rd
- Singapore 28.10.2018
- A placeholder for insert logo of sponsors (limit 10 logo)
2. POSM:
- Backdrop: 5,5m and 2,6m
- Banner: 4m and 0,5m
- Standee: 0,8m and 2m
- Cover: A4 size
3. Style:
We need style simply because we are a hospital.
Main color: light blue and a little of green (if can)

Hope to see your design soon!

Font styles to use
Sans Serif

Colors
0792cd
85cae6
86cfc6
33b8a4
33a6d7

```html
<!DOCTYPE html>
<html lang="en">
<head>
<meta charset="utf-8">
<title>Lumora Event 2018</title>
<link href="https://fonts.googleapis.com/css2?family=Montserrat:wght@200;300;400;500;600;700&display=swap" rel="stylesheet">
<style>
  :root {
    --ocean: #13618b;
    --ocean-light: #1d6d97;
    --steel: #5b8fa9;
    --sky: #6ccbef;
    --sky-soft: #85cae6;
    --mint: #93cfb1;
    --teal: #33b8a4;
    --azure: #0792cd;
    --navy: #2b4778;
    --ink: #1d5f86;
    --white: #ffffff;
  }
  * { margin: 0; padding: 0; box-sizing: border-box; }
  html, body { width: 848px; height: 1200px; overflow: hidden; background: var(--white); }
  body { font-family: "Montserrat", sans-serif; }
  .poster { position: relative; width: 848px; height: 1200px; background: var(--ocean); overflow: hidden; }
  .skyline-photo {
    position: absolute; left: 0; top: 0; width: 848px; height: 326px;
    background:
      linear-gradient(180deg, rgba(255,255,255,0) 0%, rgba(255,255,255,0) 55%, rgba(70,70,70,0.55) 62%, rgba(60,60,60,0.6) 72%, rgba(150,150,150,0.5) 80%, rgba(190,190,190,0.4) 100%),
      linear-gradient(100deg, #d9d9d9 0%, #ececec 40%, #cdcdcd 70%, #e2e2e2 100%);
  }
  .decor-band {
    position: absolute; left: 0; top: 0;
  }
  .edition { position: absolute; left: 200px; top: 248px; color: var(--white); font-weight: 700; font-size: 80px; line-height: 1; }
  .edition sup { font-size: 30px; font-weight: 600; vertical-align: 38px; margin-left: 2px; }
  .title { position: absolute; left: 290px; top: 380px; width: 320px; text-align: center; color: var(--ink); }
  .title-top { display: block; font-weight: 300; font-size: 60px; line-height: 1; padding-bottom: 10px; border-bottom: 4px solid var(--navy); }
  .title-bottom { display: block; font-weight: 600; font-size: 62px; line-height: 1; padding-top: 8px; }
  .year { position: absolute; left: 586px; top: 574px; width: 150px; text-align: center; color: var(--white); font-weight: 300; font-size: 44px; }
  .city { position: absolute; left: 80px; top: 864px; color: var(--teal); font-weight: 600; font-size: 27px; letter-spacing: 17.5px; }
  .weekday { position: absolute; left: 178px; top: 893px; color: var(--teal); font-weight: 300; font-size: 56px; letter-spacing: 1px; }
  .day { position: absolute; left: 440px; top: 842px; color: var(--azure); font-weight: 300; font-size: 114px; line-height: 1; }
  .month { position: absolute; left: 584px; top: 880px; color: var(--teal); font-weight: 400; font-size: 36px; }
  .time { position: absolute; left: 184px; top: 956px; color: var(--white); font-weight: 400; font-size: 25px; }
  .note { position: absolute; left: 307px; top: 960px; color: var(--white); font-size: 15px; line-height: 1.3; }
  .contact { position: absolute; left: 455px; top: 962px; color: var(--white); }
  .contact-label { display: block; font-size: 12px; letter-spacing: 0.3px; }
  .contact-mail { display: block; font-size: 19px; margin-top: 3px; }
  .blurb { position: absolute; left: 70px; top: 1018px; color: var(--white); font-size: 13.2px; line-height: 1.42; white-space: nowrap; }
  .blurb span { display: block; }
  .sponsors {
    position: absolute; left: 0; top: 1097px; width: 848px; height: 103px; background: var(--white);
    display: flex; align-items: center; justify-content: space-between; padding: 0 30px;
  }
  .sponsor { display: flex; align-items: center; gap: 4px; color: var(--navy); font-weight: 700; font-size: 12px; line-height: 1.1; text-align: center; max-width: 78px; }
  .sponsor-dot { width: 8px; height: 8px; background: var(--navy); flex: none; }
</style>
</head>
<body>
<main class="poster">
  <div class="skyline-photo" role="img" aria-label="Black and white photo of the Singapore waterfront skyline"></div>

  <svg class="decor-band" width="848" height="1097" viewBox="0 0 848 1097" role="img" aria-label="Abstract decorative shapes around the event title">
    <defs>
      <linearGradient id="band-fade" x1="0" y1="1" x2="1" y2="0">
        <stop offset="0" stop-color="#93cfb1"/>
        <stop offset="1" stop-color="#6ccbef"/>
      </linearGradient>
    </defs>
    <circle cx="120" cy="780" r="60" fill="var(--ocean-light)"/>
    <circle cx="720" cy="720" r="58" fill="var(--ocean-light)"/>
    <rect x="-420" y="-40" width="840" height="80" rx="40" fill="url(#band-fade)" transform="translate(460 420) rotate(-42)"/>
    <circle cx="745" cy="450" r="100" fill="none" stroke="var(--mint)" stroke-width="7"/>
    <circle cx="450" cy="460" r="256" fill="var(--steel)"/>
    <circle cx="450" cy="450" r="192" fill="var(--white)"/>
    <circle cx="230" cy="290" r="100" fill="var(--mint)"/>
    <circle cx="660" cy="600" r="96" fill="var(--sky)"/>
    <circle cx="660" cy="600" r="80" fill="none" stroke="var(--navy)" stroke-width="4"/>
  </svg>

  <div class="edition">3<sup>rd</sup></div>
  <h1 class="title"><span class="title-top">Lumora</span><span class="title-bottom">Event</span></h1>
  <div class="year">2018</div>

  <div class="city">SINGAPORE</div>
  <div class="weekday">SUNDAY</div>
  <div class="day">28</div>
  <div class="month">OCTOBER</div>
  <div class="time">6:30pm</div>
  <p class="note">Students set up<br>in the cafeteria</p>
  <p class="contact"><span class="contact-label">QUESTIONS? CONTACT</span><span class="contact-mail">hello@lumoraevent.org</span></p>
  <p class="blurb">
    <span>At vero eos et accusamus et iusto odio dignissimos ducimus qui blanditiis praesentium voluptatum</span>
    <span>deleniti atque corrupti quos dolores et quas molestias excepturi sint occaecati cupiditate non provident,</span>
    <span>similique sunt in culpa qui officia deserunt mollitia animi, id est laborum et dolorum fuga.</span>
  </p>

  <footer class="sponsors">
    <span class="sponsor"><span class="sponsor-dot"></span>Bluebank Trips</span>
    <span class="sponsor">Pinecrest Build</span>
    <span class="sponsor">Fernleaf Farm</span>
    <span class="sponsor">Orvix</span>
    <span class="sponsor">Malt Hall</span>
    <span class="sponsor">Northriver Paddle Club</span>
    <span class="sponsor">trailwise</span>
    <span class="sponsor">Halden Spirits</span>
    <span class="sponsor">Westwater Canoe</span>
    <span class="sponsor"><span class="sponsor-dot"></span>Tier Nine</span>
  </footer>
</main>
</body>
</html>
```